Designing a brochures for an educational counseling service provider

We would like a 4 sided design on a 11x8.5 paper, half folded. I have including a sample design we did to give you an idea of what we envision but we welcome creativity to make beautiful looking flyers. Text for the flier is included as well as our logo.
- The most important thing is capturing our audience/market. We will be handing these flies to schools, organizations and individual clients.

www.pvrlearningadvisors.example

Target Market(s)

We are targeting international students wanting to study in the U.S and Canada.

Industry/Entity Type

Education

Requirements
Must have
• - Clean and clear
• - Our logo should visible and well placed.
• - Could you the pictures of students, libraries and school buildings or you could use the pictures we already have.
Nice to have
• We would like this to match business cards.

```html
<!DOCTYPE html>
<html lang="en">
<head>
<meta charset="utf-8">
<title>PVR Learning Advisors – Brochure Spread</title>
<link href="https://fonts.googleapis.com/css2?family=Lato:wght@400;700&family=Oswald:wght@400;500&display=swap" rel="stylesheet">
<style>
  :root{
    --blue:#1a82d0;
    --blue-dark:#0f6bb3;
    --green:#4aad3a;
    --green-dark:#3a962c;
    --text:#3c3c3c;
    --paper:#ffffff;
    --backdrop:#ececec;
    --photo-warm:#8a6450;
    --photo-deep:#4a342b;
    --photo-light:#d8cbb8;
  }
  *{box-sizing:border-box;margin:0;padding:0}
  html,body{width:960px;height:1200px;overflow:hidden;background:var(--backdrop)}
  body{position:relative;font-family:'Lato',sans-serif;color:var(--text)}
  .spread{position:absolute;left:30px;top:253px;width:900px;height:694px;background:var(--paper);box-shadow:0 6px 18px rgba(0,0,0,.25);overflow:hidden}
  .panel{position:absolute;top:0;height:100%}
  .panel--inside{left:0;width:450px;background:linear-gradient(90deg,#e9e9e9 0%,#fafafa 55%,#e4e4e4 100%)}
  .panel--cover{left:450px;width:450px;background:var(--paper);z-index:2}

  .about-title{position:absolute;left:31px;top:44px;font-family:'Oswald',sans-serif;font-weight:400;font-size:21px;color:var(--blue)}
  .about-copy{position:absolute;left:31px;width:372px;font-size:13.2px;line-height:16.2px;text-align:justify}
  .about-copy--mission{top:82px}
  .about-copy--family{top:408px}

  .portrait{position:absolute;top:233px;width:163px;height:163px;border-radius:50%;border:6px solid var(--blue);box-shadow:0 0 0 4px var(--green)}
  .portrait--student{left:28px;background:linear-gradient(180deg,#cfc7b8 0%,#9c7a64 45%,#f1f1ee 80%)}
  .portrait--advisor{left:224px;background:linear-gradient(180deg,#6e5a4a 0%,#b08468 45%,#8a4e46 80%)}

  .footer-band{position:absolute;left:0;top:582px;width:900px;height:4px;background:var(--green);z-index:1}
  .contact-block{position:absolute;left:0;top:586px;width:410px;height:108px;background:var(--paper);border-top-right-radius:34px;z-index:1}
  .brand{display:flex;align-items:center;gap:6px;font-family:'Lato',sans-serif;font-weight:700;color:var(--blue)}
  .brand__dot{width:14px;height:14px;border-radius:50%;background:var(--green);flex:none}
  .contact-block .brand{position:absolute;left:26px;top:32px;font-size:13px;line-height:15px;width:130px}
  .contact-list{position:absolute;left:176px;top:16px;font-size:11px;line-height:13.4px;list-style:none}

  .hanger{position:absolute;top:0;width:2px;height:124px;background:#555}
  .hanger--l{left:83px}.hanger--r{left:370px}
  .cover-brand{position:absolute;left:0;width:450px;top:62px;justify-content:center;font-size:26px}
  .cover-brand .brand__dot{width:24px;height:24px}
  .sign{position:absolute;left:38px;top:122px;width:372px;height:143px;border-radius:14px;background:linear-gradient(180deg,#5cbf47,var(--green-dark));border:3px solid #fff;box-shadow:0 0 0 2px #8ccf7d,0 4px 8px rgba(0,0,0,.2);display:flex;align-items:center;justify-content:center;text-align:center}
  .sign__pin{position:absolute;top:8px;width:11px;height:11px;border-radius:50%;background:#fff}
  .sign__pin--l{left:38px}.sign__pin--r{right:34px}
  .sign__headline{font-family:'Oswald',sans-serif;font-weight:500;font-size:23px;line-height:33px;color:#fff;letter-spacing:-.3px;margin-top:6px}

  .cover-photo{position:absolute;left:0;top:277px;width:450px;height:305px;background:linear-gradient(180deg,#ece8e0 0%,var(--photo-warm) 22%,var(--photo-deep) 55%,var(--photo-warm) 78%,var(--photo-light) 100%)}
  .service-band{position:absolute;left:0;top:586px;width:450px;height:108px;background:linear-gradient(180deg,var(--blue),var(--blue-dark))}
  .cover-rule{position:absolute;left:0;top:582px;width:450px;height:4px;background:var(--green)}
  .services{position:absolute;left:0;top:537px;width:450px;display:flex;justify-content:space-around;padding:0 12px;list-style:none;z-index:3}
  .service{width:100px;text-align:center;color:#fff;font-size:13.5px;line-height:16px}
  .service__icon{width:72px;height:72px;margin:0 auto 10px;border-radius:50%;background:#fff;border:3px solid #cfe3f5;box-shadow:0 2px 5px rgba(0,0,0,.25);display:flex;align-items:center;justify-content:center}
</style>
</head>
<body>
<main class="spread">
  <section class="panel panel--inside">
    <h2 class="about-title">About Us</h2>
    <p class="about-copy about-copy--mission">Our mission is to make quality education accessible and affordable to the families we serve. Our services are designed with the child's future in mind. Whether one is seeking an academic or non-academic environment, it is important to us that we set our clients up for success.</p>
    <div class="portrait portrait--student" role="img" aria-label="Portrait photo of a smiling student"></div>
    <div class="portrait portrait--advisor" role="img" aria-label="Portrait photo of a consultant in a library"></div>
    <p class="about-copy about-copy--family">We are a family-centered organization and our goals are the same as those of our clients; for their child to thrive and reach their goals and dreams. With over 10 years of experience in the business, we are aware of the financial obstacles created by the ever increasing cost in education. Our expert consultants work closely with families to map out their educational budget and find the best affordable and quality educational options.</p>
  </section>

  <section class="panel panel--cover">
    <span class="hanger hanger--l"></span><span class="hanger hanger--r"></span>
    <div class="brand cover-brand"><span class="brand__dot"></span>PVR Learning Advisors</div>
    <div class="sign">
      <span class="sign__pin sign__pin--l"></span><span class="sign__pin sign__pin--r"></span>
      <h1 class="sign__headline">A full-service international<br>educational consulting group serving<br>students and families across the globe</h1>
    </div>
    <div class="cover-photo" role="img" aria-label="Photo of four smiling students gathered around open books"></div>
    <div class="cover-rule"></div>
    <div class="service-band"></div>
    <ul class="services">
      <li class="service">
        <div class="service__icon"><svg width="36" height="36" viewBox="0 0 36 36" fill="none" stroke="#888" stroke-width="2"><path d="M4 13 18 5l14 8z"/><path d="M7 15v13M13 15v13M18 15v13M23 15v13M29 15v13"/><path d="M4 30h28"/></svg></div>
        BOARDING<br>SCHOOLS</li>
      <li class="service">
        <div class="service__icon"><svg width="36" height="36" viewBox="0 0 36 36" fill="none" stroke="#888" stroke-width="2"><path d="M8 4h14l6 6v22H8z"/><path d="M22 4v6h6"/><path d="M14 26l10-10 3 3-10 10h-3z"/></svg></div>
        COLLEGE<br>ADMISSION</li>
      <li class="service">
        <div class="service__icon"><svg width="36" height="36" viewBox="0 0 36 36" fill="none" stroke="#888" stroke-width="2"><circle cx="12" cy="10" r="4"/><path d="M5 22c0-5 14-5 14 0"/><circle cx="25" cy="17" r="4"/><path d="M18 29c0-5 14-5 14 0"/><path d="M4 24h14"/></svg></div>
        TRANSFER<br>STUDENTS</li>
      <li class="service">
        <div class="service__icon"><svg width="36" height="36" viewBox="0 0 36 36" fill="none" stroke="#888" stroke-width="2"><path d="M3 14 18 7l15 7-15 7z"/><path d="M10 18v7c4 4 12 4 16 0v-7"/><path d="M31 15v9"/></svg></div>
        GRADUATE<br>STUDENTS</li>
    </ul>
  </section>

  <div class="footer-band"></div>
  <div class="contact-block">
    <div class="brand"><span class="brand__dot"></span>PVR Learning Advisors</div>
    <ul class="contact-list">
      <li>555-214-0193</li>
      <li>nadia@pvrlearningadvisors.example</li>
      <li>PVR Learning Advisors,</li>
      <li>LLC, 1180 Harbor Rd</li>
      <li>Suite 30B, Lakeview, OR 97630</li>
    </ul>
  </div>
</main>
</body>
</html>
```